NEW! Sports Supplement label
Peak Cellular Dynamics
Project: NEW! Sports Supplement label
NEW! Sports Supplement label - Sports
Creative Brief
Looking for a new packaging design for a new line of products. This needs to be a clean label that delivers a scientific or medical feel in 3 colors with 4 lines for product descriptor sublines. <p><p> For Example: <p> • Muscle Recovery Acceleration <p> • Nitric Oxide Production <p> • Maximum Muscle Mass <p> • Improved Energy &amp; Focus <p><p> Use the following elements for presentation: <p><p> Name: PC250Z <p><p> 120 Capsules Dietary Supplement <p><p> The products are geared to Sports Supplements, Fat burners, preworkout supplements, sport drinks. <p><p> The fonts for the Product name and PCD logo must be destinctive elements and pop that adds value by providing consumers with instantly recognizable cues to help with the purchase decision making process. Preferrably reversed out white or black. <p> <p> Please see the following sites as example product labels for creative thought. They also provide actual full labels for your review: <p><p> http://www.vitrelmart.com/product/index.jsp?productId=58204417 http://www.vitrelmart.com/product/index.jsp?productId=58391026 http://www.vitrelmart.com/product/index.jsp?productId=58645139 <p><p> The label should be clean, in that it provides a clear, attractive space, with key information (4 line product descriptor mentioned above) on the front display panel necessary for a consumer to make a quick purchase decision. <p> The label should communicate a concise but informative message designed to make the consumer feel comfortable with the product by providing consumers with instantly recognizable cues (symbols of quality) to help with the purchase decision making process.
Sports
Sports nutrition products target a mass audience of consumers who have grown up knowing an active lifestyle has positive, long-term implications for health, fitness, weight management and longevity.
Please provide label design with color codes and in standard file formats with element layers. 2.75 x 7.00 4 x 9.375

```html
<!DOCTYPE html>
<html lang="en">
<head>
<meta charset="utf-8">
<title>PC250Z Dietary Supplement Label</title>
<link rel="stylesheet" href="https://fonts.googleapis.com/css2?family=Roboto:ital,wght@0,500;0,700;0,900;1,700&family=Fira+Sans:wght@600;700&display=swap">
<style>
  :root {
    --ink: #0c0c0c;
    --silver-light: #f4f4f4;
    --silver-mid: #d6d6d6;
    --silver-dark: #9a9a9a;
    --band-dark: #3a3a3a;
    --brand-grey: #6e6e6e;
    --accent-red: #d0161b;
    --panel-white: #ffffff;
    --badge-grey: #6a6a6a;
  }
  html, body {
    margin: 0;
    padding: 0;
    width: 1200px;
    height: 929px;
    overflow: hidden;
    background: #ffffff;
  }
  .label {
    position: relative;
    width: 1200px;
    height: 929px;
    overflow: hidden;
    background:
      repeating-linear-gradient(125deg, rgba(255,255,255,0) 0 60px, rgba(255,255,255,0.35) 60px 90px, rgba(255,255,255,0) 90px 170px),
      linear-gradient(90deg, var(--silver-dark) 0%, var(--silver-light) 22%, var(--silver-mid) 50%, var(--silver-light) 78%, var(--silver-dark) 100%);
    font-family: "Roboto", Arial, sans-serif;
  }
  .band-top, .band-bottom {
    position: absolute;
    left: 0;
    width: 100%;
    background: linear-gradient(90deg, #1e1e1e, var(--band-dark) 30%, #5a5a5a 50%, var(--band-dark) 70%, #1e1e1e);
    z-index: 2;
  }
  .band-top { top: 0; height: 48px; border-bottom: 4px solid #bdbdbd; }
  .band-bottom { bottom: 0; height: 36px; border-top: 4px solid #bdbdbd; }

  .brand {
    position: absolute;
    top: 64px;
    left: 0;
    width: 100%;
    text-align: center;
  }
  .brand-mark {
    font-weight: 700;
    font-size: 82px;
    line-height: 1;
    color: var(--ink);
    letter-spacing: 1px;
  }
  .brand-name {
    margin-top: 10px;
    font-weight: 700;
    font-size: 29px;
    color: var(--brand-grey);
    letter-spacing: 0.5px;
  }

  .product-name {
    position: absolute;
    top: 250px;
    left: 0;
    width: 100%;
    margin: 0;
    text-align: center;
    font-weight: 900;
    font-size: 210px;
    line-height: 1;
    letter-spacing: 0;
    color: var(--ink);
  }

  .descriptor-bar {
    position: absolute;
    top: 460px;
    left: 390px;
    width: 650px;
    height: 56px;
    background: var(--ink);
    clip-path: polygon(0 0, 100% 0, 96% 100%, 0 100%);
    color: #ffffff;
    font-style: italic;
    font-weight: 700;
    font-size: 44px;
    line-height: 56px;
    text-align: center;
    letter-spacing: 1px;
  }

  .benefit-panel {
    position: absolute;
    top: 548px;
    left: 113px;
    width: 974px;
    height: 400px;
    background: var(--panel-white);
    border-radius: 26px;
    box-shadow: 0 0 10px rgba(0,0,0,0.2);
  }
  .benefit-list {
    list-style: none;
    margin: 0;
    padding: 58px 0 0 44px;
    font-family: "Fira Sans", Arial, sans-serif;
    font-weight: 600;
    font-size: 36px;
    color: var(--ink);
  }
  .benefit-list li {
    display: flex;
    align-items: center;
    height: 47px;
  }
  .benefit-list svg { width: 22px; height: 24px; margin-right: 18px; flex: none; }

  .count-badge {
    position: absolute;
    top: 743px;
    left: 879px;
    width: 170px;
    height: 160px;
    background: var(--badge-grey);
    border-radius: 22px;
    color: #ffffff;
    text-align: center;
  }
  .count-number {
    font-weight: 700;
    font-size: 88px;
    line-height: 1;
    margin-top: 12px;
  }
  .count-unit {
    font-weight: 700;
    font-size: 26px;
    margin-top: 2px;
  }
</style>
</head>
<body>
<main class="label">
  <div class="band-top"></div>

  <header class="brand">
    <div class="brand-mark">PCD</div>
    <div class="brand-name">PEAK CELLULAR DYNAMICS</div>
  </header>

  <h1 class="product-name">PC250Z</h1>

  <div class="descriptor-bar">DIETARY SUPPLEMENT</div>

  <section class="benefit-panel">
    <ul class="benefit-list">
      <li><svg viewBox="0 0 22 24"><path d="M2 2 L20 12 L2 22 L8 12 Z" fill="#d0161b"/></svg>Muscle Recovery Acceleration</li>
      <li><svg viewBox="0 0 22 24"><path d="M2 2 L20 12 L2 22 L8 12 Z" fill="#d0161b"/></svg>NItric Oxide Production</li>
      <li><svg viewBox="0 0 22 24"><path d="M2 2 L20 12 L2 22 L8 12 Z" fill="#d0161b"/></svg>Maximum Musle Mass</li>
      <li><svg viewBox="0 0 22 24"><path d="M2 2 L20 12 L2 22 L8 12 Z" fill="#d0161b"/></svg>Improved Energy &amp; Focus</li>
    </ul>
  </section>

  <div class="count-badge">
    <div class="count-number">30</div>
    <div class="count-unit">CAPSULES</div>
  </div>

  <div class="band-bottom"></div>
</main>
</body>
</html>
```